Bed Company needs business card

Hello, we are a bed company that makes specialized magnets for beds. We are an alternative healing company. I need a modern and upscale business card. Please incorporate my logo for the card.

Accepted file formats are AI, EPS, and Press-Ready PDFS.

Please include all fonts or convert them to outlines regardless of file type.

If you are designing the card in Photoshop the file Must be 1200dpi.

I am open to anything for the business card.  I really like all of your designs and if you want to change the color of the logo, you can.  I will be making the final selection by Friday.  Thank You for all of your designs.  Feel Free to submit different color logos if you want.  

Reason: I will make a decision Final on Friday April 20th. 2012. Good Luck and Thank you all for the designs.

Target Market(s)

My target Market is people, who are looking for alternative healing.

Industry/Entity Type

Business

Requirements
Must have
• My logo must be incorporated. The front card must have

Name
Job Title

Address
Work
Cell
Fax
email
web

Just put in fake info for the card.

The back of the card. I want the logo on the back with color. I just want it to look modern and cool.

```html
<!DOCTYPE html>
<html lang="en">
<head>
<meta charset="utf-8">
<title>Restfield Business Card</title>
<link rel="stylesheet" href="https://fonts.googleapis.com/css2?family=Open+Sans:wght@400;700&display=swap">
<style>
  :root {
    --backdrop: #e6e4e1;
    --paper: #ffffff;
    --green: #52b748;
    --green-deep: #0e6a37;
    --brand-green: #2e9b3f;
    --ink: #3b3b3b;
    --ink-soft: #4a4a4a;
  }
  * { box-sizing: border-box; margin: 0; padding: 0; }
  html, body {
    width: 1200px;
    height: 900px;
    overflow: hidden;
    background: var(--backdrop);
    font-family: "Open Sans", Arial, sans-serif;
    color: var(--ink);
  }
  .card {
    position: absolute;
    width: 620px;
    height: 354px;
    background: var(--paper);
    box-shadow: 0 6px 18px rgba(0,0,0,0.18);
    overflow: hidden;
  }
  .card--front { left: 110px; top: 80px; }
  .card--back { left: 470px; top: 466px; }

  .pattern-panel {
    position: absolute;
    top: 0;
    right: 0;
    height: 100%;
    background: linear-gradient(135deg, var(--green-deep) 0%, var(--green) 35%, var(--green) 70%, var(--green-deep) 100%);
  }
  .card--front .pattern-panel { width: 285px; }
  .card--back .pattern-panel { width: 290px; }

  .holder-name {
    position: absolute;
    left: 62px;
    top: 84px;
    font-size: 31px;
    font-weight: 400;
    color: var(--ink);
    letter-spacing: 0.2px;
  }
  .holder-title {
    position: absolute;
    left: 128px;
    top: 124px;
    font-size: 17px;
    color: var(--green-deep);
  }
  .accent-bar {
    position: absolute;
    left: 40px;
    top: 180px;
    width: 5px;
    height: 144px;
    background: var(--green);
  }
  .contact-list {
    position: absolute;
    left: 68px;
    top: 180px;
    font-size: 13.5px;
    line-height: 19px;
    color: var(--ink-soft);
    list-style: none;
  }
  .contact-list .label {
    display: inline-block;
    width: 34px;
  }
  .contact-list .sep {
    display: inline-block;
    width: 20px;
  }
  .contact-email {
    position: absolute;
    left: 68px;
    top: 242px;
    font-size: 14px;
    color: var(--ink-soft);
  }
  .event-address {
    position: absolute;
    left: 70px;
    top: 282px;
    font-size: 10px;
    line-height: 15px;
    color: var(--ink-soft);
  }
  .web-address {
    position: absolute;
    right: 14px;
    bottom: 14px;
    font-size: 12px;
    color: var(--paper);
    letter-spacing: 0.3px;
  }

  .brand {
    position: absolute;
    left: 52px;
    top: 112px;
    display: flex;
    align-items: center;
    gap: 12px;
  }
  .brand-square {
    width: 34px;
    height: 34px;
    background: var(--brand-green);
  }
  .brand-name {
    font-size: 30px;
    font-weight: 700;
    color: var(--brand-green);
    letter-spacing: 0.3px;
  }
</style>
</head>
<body>

  <section class="card card--front" aria-label="Business card front">
    <h1 class="holder-name">Daniel Hart</h1>
    <p class="holder-title">director</p>
    <div class="accent-bar"></div>
    <ul class="contact-list">
      <li><span class="label">tel</span><span class="sep">:</span>(555) 214 870</li>
      <li><span class="label">cell</span><span class="sep">:</span>(555) 214 871</li>
      <li><span class="label">fax</span><span class="sep">:</span>(555) 214 872</li>
    </ul>
    <p class="contact-email">office@restfield.com</p>
    <p class="event-address">May 14-17, 2013, Lakeside Hall West,<br>Riverton OR, Booth 208</p>
    <div class="pattern-panel" role="img" aria-label="Large geometric cross emblem in light and dark green blocks">
      <p class="web-address">www.restfield-sleep.com</p>
    </div>
  </section>

  <section class="card card--back" aria-label="Business card back">
    <div class="brand">
      <span class="brand-square"></span>
      <span class="brand-name">Restfield</span>
    </div>
    <div class="pattern-panel" role="img" aria-label="Large geometric cross emblem in light and dark green blocks"></div>
  </section>

</body>
</html>
```